Dovetree baby skincare

design business cards (double sided) and complimentary note (single sided)

Industry/Entity Type

Business

Colors

Designer to choose colors to be used in the design.

```html
<!DOCTYPE html>
<html lang="en">
<head>
<meta charset="utf-8">
<title>Dovetree baby skincare – business card</title>
<link rel="stylesheet" href="https://fonts.googleapis.com/css2?family=Source+Sans+3:wght@300;400;600&display=swap">
<style>
  :root {
    --backdrop: #e9e9e8;
    --card: #f7f7f6;
    --peach: #f3cfb4;
    --peach-soft: #f8e0cd;
    --peach-wash-light: rgba(236, 190, 155, 0.25);
    --peach-wash: rgba(236, 190, 155, 0.75);
    --gold: #c9a340;
    --ink: #3a3a3a;
    --ink-soft: #666666;
  }
  * { margin: 0; padding: 0; box-sizing: border-box; }
  html, body { width: 1200px; height: 800px; overflow: hidden; }
  body {
    background: var(--backdrop);
    font-family: "Source Sans 3", sans-serif;
    position: relative;
  }
  .card {
    position: absolute;
    top: 250px;
    width: 510px;
    height: 300px;
    background: var(--card);
    overflow: hidden;
    box-shadow: 0 6px 18px rgba(0,0,0,0.12);
  }
  .card--front { left: 60px; }
  .card--back { left: 630px; }
  .wave {
    position: absolute;
    left: 0;
    width: 100%;
    height: 70px;
  }
  .wave--top { top: 0; }
  .wave--bottom { bottom: 0; transform: rotate(180deg); }
  .wave .band-light { fill: var(--peach-soft); }
  .wave .band-main { fill: var(--peach); }

  .brand-name {
    position: absolute;
    font-family: "Source Sans 3", sans-serif;
    font-weight: 600;
    color: var(--gold);
    line-height: 1;
    white-space: nowrap;
  }
  .card--front .brand-name {
    left: 0; right: 0;
    top: 108px;
    text-align: center;
    font-size: 84px;
    letter-spacing: -1px;
  }
  .card--back .brand-name {
    left: 38px;
    bottom: 76px;
    font-size: 42px;
    letter-spacing: -0.5px;
  }

  .watercolour-swatch {
    position: absolute;
    left: 222px;
    top: 150px;
    width: 52px;
    height: 100px;
    background: linear-gradient(180deg, var(--peach-wash-light), var(--peach-wash) 55%, var(--peach-wash-light));
  }

  .contact {
    position: absolute;
    left: 290px;
    top: 62px;
    color: var(--ink);
    font-size: 14px;
    line-height: 1.3;
  }
  .contact__name {
    font-size: 21px;
    font-weight: 400;
    margin-bottom: 2px;
  }
  .contact__role {
    font-weight: 300;
    color: var(--ink-soft);
  }
  .contact__line { font-weight: 400; }
</style>
</head>
<body>

  <section class="card card--front" aria-label="Business card front">
    <svg class="wave wave--top" viewBox="0 0 510 70" preserveAspectRatio="none" aria-hidden="true">
      <path class="band-light" d="M0 0 H510 V44 C470 56 440 34 400 42 C350 52 320 30 270 38 C220 46 190 30 140 36 C90 42 50 30 0 38 Z"/>
      <path class="band-main" d="M0 0 H510 V30 C470 40 440 20 400 28 C350 38 320 16 270 24 C220 32 190 16 140 22 C90 28 50 16 0 24 Z"/>
    </svg>
    <div class="brand-name">Dovetree</div>
    <svg class="wave wave--bottom" viewBox="0 0 510 70" preserveAspectRatio="none" aria-hidden="true">
      <path class="band-light" d="M0 0 H510 V44 C470 56 440 34 400 42 C350 52 320 30 270 38 C220 46 190 30 140 36 C90 42 50 30 0 38 Z"/>
      <path class="band-main" d="M0 0 H510 V30 C470 40 440 20 400 28 C350 38 320 16 270 24 C220 32 190 16 140 22 C90 28 50 16 0 24 Z"/>
    </svg>
  </section>

  <section class="card card--back" aria-label="Business card back">
    <svg class="wave wave--top" viewBox="0 0 510 70" preserveAspectRatio="none" aria-hidden="true">
      <path class="band-light" d="M0 0 H510 V36 C470 46 440 26 400 34 C350 44 320 22 270 30 C220 38 190 22 140 28 C90 34 50 22 0 30 Z"/>
      <path class="band-main" d="M0 0 H510 V22 C470 32 440 12 400 20 C350 30 320 8 270 16 C220 24 190 8 140 14 C90 20 50 8 0 16 Z"/>
    </svg>

    <div class="contact">
      <p class="contact__name">Maren Holt-Ashby</p>
      <p class="contact__role">CEO</p>
      <p class="contact__line">9041 2278</p>
      <p class="contact__line">0412 550 913</p>
      <p class="contact__line">maren@dovetreeskincare.com</p>
      <p class="contact__line">www.dovetreeskincare.com</p>
    </div>

    <div class="watercolour-swatch" role="img" aria-label="Peach watercolour brush swatch"></div>
    <div class="brand-name">Dovetree</div>

    <svg class="wave wave--bottom" viewBox="0 0 510 70" preserveAspectRatio="none" aria-hidden="true">
      <path class="band-light" d="M0 0 H510 V36 C470 46 440 26 400 34 C350 44 320 22 270 30 C220 38 190 22 140 28 C90 34 50 22 0 30 Z"/>
      <path class="band-main" d="M0 0 H510 V22 C470 32 440 12 400 20 C350 30 320 8 270 16 C220 24 190 8 140 14 C90 20 50 8 0 16 Z"/>
    </svg>
  </section>

</body>
</html>
```